Redesign for existing homepage

We would like a redesign for our websites 2 column homepage
We provide engine repair and reconditioning services
We would like a cleaner, modern site that works well with our logo colors
Please see the attached brief for more info
Target Market(s)
25 - 45
Industry/Entity Type
Cleaner
Requirements
Must have
- Google Fonts

```html
<!DOCTYPE html>
<html lang="en">
<head>
<meta charset="utf-8">
<title>Harlow Bay Engine Reconditioners</title>
<link href="https://fonts.googleapis.com/css2?family=Open+Sans:wght@400;600&display=swap" rel="stylesheet">
<style>
:root{
  --dark:#2a2a2a;
  --dark-line:#3a3a3a;
  --blue:#0f62fa;
  --blue-deep:#0048e0;
  --orange:#e8a84a;
  --orange-deep:#e38f2c;
  --accent:#ef7d1a;
  --text:#555;
  --muted:#999;
  --field-border:#d8d8d8;
  --panel:#f4f4f4;
}
*{box-sizing:border-box;margin:0;padding:0}
html,body{width:1186px;height:1200px;overflow:hidden}
body{font-family:"Open Sans",sans-serif;color:var(--text);background:#fff;position:relative}
.wrap{width:1000px;margin:0 auto;position:relative}

.site-header{background:var(--dark);height:137px}
.site-header .wrap{height:137px;display:flex;justify-content:space-between;align-items:center}
.brand{display:flex;align-items:center;gap:12px;font-size:22px;font-weight:600;color:#f2a93b}
.brand-dot{width:26px;height:26px;border-radius:50%;background:var(--blue)}
.contact{display:flex;align-items:center;gap:12px;text-align:right}
.contact .tagline{color:#ccc;font-size:15px}
.contact .phone{color:#f2a93b;font-size:19px}

.main-nav{background:linear-gradient(var(--blue),var(--blue-deep));height:47px;border-bottom:1px solid #0039b5}
.main-nav ul{list-style:none;display:flex;height:46px}
.main-nav li{border-right:1px solid #0a3fb0;display:flex;align-items:center;padding:0 19px;color:#fff;font-size:13px}
.main-nav li:first-child{border-left:1px solid #0a3fb0}
.main-nav li.active{background:linear-gradient(#f0b14f,#e3952f);color:#333;padding:0 26px}

.hero{display:flex;gap:9px;margin-top:19px;height:330px}
.slider{width:726px;height:330px;position:relative;background:linear-gradient(135deg,#8a8a8a,#3c3c3c 55%,#1e1e1e)}
.slider .arrow{position:absolute;top:145px;width:28px;height:28px;border-radius:50%;background:#fff;display:flex;align-items:center;justify-content:center}
.slider .arrow.prev{left:27px}.slider .arrow.next{right:19px}
.caption{position:absolute;right:20px;bottom:15px;background:rgba(0,0,0,.65);color:#fff;font-size:18px;padding:4px 18px}
.promo{width:265px;display:flex;flex-direction:column}
.promo-item{flex:1;display:flex;align-items:center;gap:20px;padding:0 22px 0 18px;color:#fff;font-size:18px;line-height:22px;background:linear-gradient(var(--orange),var(--orange-deep));border-bottom:2px solid #f0bd74}
.promo-item:last-child{border-bottom:0}
.promo-item svg{flex:none}

.content{display:flex;gap:9px;margin-top:27px}
.intro{width:726px;padding-left:3px}
.intro h1{font-weight:400;color:var(--accent);font-size:26px;line-height:30px}
.intro h2{font-weight:400;color:#444;font-size:20px;margin:2px 0 14px}
.intro p{font-size:13px;line-height:20px}
.checklist{list-style:none;margin-top:18px}
.checklist li{font-size:14px;line-height:30px}
.checklist li::before{content:"•";font-size:10px;margin-right:8px;color:#888}
.partners{display:flex;gap:24px;align-items:center;margin-top:20px}
.badge-square{width:77px;height:92px;background:#ffee10}
.badge-oval{width:116px;height:72px;border-radius:50%;background:#111}

.quote{width:264px;background:var(--panel);height:421px}
.quote h3{background:linear-gradient(var(--blue),var(--blue-deep));color:#fff;font-weight:400;font-size:18px;padding:8px 25px;height:44px}
.quote form{padding:15px 25px}
.field{height:32px;border:1px solid var(--field-border);background:#fff;margin-bottom:10px;font-size:13px;color:var(--muted);padding:7px 10px;display:flex;justify-content:space-between}
.field.select span:last-child{border-left:1px solid var(--field-border);padding-left:8px}
.trade{font-size:12px;color:var(--muted);margin:18px 2px 14px;display:flex;align-items:center;gap:8px}
.trade .box{width:12px;height:12px;border:1px solid #999;background:#fff}
.trade b{font-weight:400;color:#555;font-size:14px}
.field.area{height:92px}
.submit{display:block;margin:12px 0 0 auto;background:linear-gradient(#f0b14f,#e3952f);color:#333;font-size:12px;padding:8px 11px;width:68px}

.site-footer{position:absolute;left:0;right:0;top:1040px;bottom:0;background:var(--dark)}
.foot-nav{list-style:none;display:flex;justify-content:space-between;padding:28px 12px 20px;border-bottom:1px solid var(--dark-line)}
.foot-nav li{color:#aaa;font-size:13px}
.foot-nav li::before{content:"•";margin-right:3px;font-size:9px}
.foot-bottom{display:flex;justify-content:space-between;align-items:center;padding-top:16px}
.copy{color:#bbb;font-size:13px}
.social{display:flex;gap:8px}
.social span{width:36px;height:36px;border-radius:50%;border:2px solid #111}
</style>
</head>
<body>
<header class="site-header">
  <div class="wrap">
    <div class="brand"><span class="brand-dot"></span>Harlow Bay Engine Reconditioners</div>
    <div class="contact">
      <div><div class="tagline">Engine repairs &amp; Reconditionin specialists</div>
      <div class="phone">Greater Wellington - (04) 555 0182</div></div>
      <svg width="32" height="32" viewBox="0 0 24 24"><path fill="#ccc" d="M6.6 10.8a15 15 0 0 0 6.6 6.6l2.2-2.2c.3-.3.7-.4 1-.2 1.1.4 2.3.6 3.6.6.6 0 1 .4 1 1V20c0 .6-.4 1-1 1A17 17 0 0 1 3 4c0-.6.4-1 1-1h3.5c.6 0 1 .4 1 1 0 1.3.2 2.5.6 3.6.1.3 0 .7-.2 1z"/></svg>
    </div>
  </div>
</header>

<nav class="main-nav">
  <div class="wrap">
    <ul>
      <li class="active">Home</li><li>About us</li><li>Private Vehicle Service &amp; Repair</li><li>Trade Customers</li><li>Race &amp; Classic Car Engine</li><li>Make an Enquiry</li><li>Contact us</li>
    </ul>
  </div>
</nav>

<main class="wrap">
  <section class="hero">
    <div class="slider" role="img" aria-label="Photo of hands working on a car engine with a socket wrench">
      <span class="arrow prev"><svg width="10" height="10" viewBox="0 0 10 10"><path d="M7 1L3 5l4 4" stroke="#888" fill="none" stroke-width="1.5"/></svg></span>
      <span class="arrow next"><svg width="10" height="10" viewBox="0 0 10 10"><path d="M3 1l4 4-4 4" stroke="#888" fill="none" stroke-width="1.5"/></svg></span>
      <div class="caption">Phasellus consectetur, odio quis consectetur</div>
    </div>
    <div class="promo">
      <div class="promo-item">
        <svg width="40" height="40" viewBox="0 0 24 24"><path fill="#fff" d="M21 6.5a5 5 0 0 1-6.7 4.7L6 19.5a2 2 0 0 1-2.8-2.8l8.3-8.3A5 5 0 0 1 17.5 3l-3 3 .6 2.9 2.9.6 3-3z"/></svg>
        <span>Need service &amp; repair for a private vehicle?</span></div>
      <div class="promo-item">
        <svg width="40" height="40" viewBox="0 0 24 24"><circle cx="12" cy="7" r="4.5" fill="#fff"/><path fill="#fff" d="M3 22c0-5 4-8 9-8s9 3 9 8z"/></svg>
        <span>Interested in becoming a trade customer?</span></div>
      <div class="promo-item">
        <svg width="48" height="36" viewBox="0 0 32 24"><path fill="#fff" d="M2 12l3-1 4-6h12l5 6 4 1v6H2z"/><circle cx="8" cy="18" r="3" fill="#e39a3a" stroke="#fff" stroke-width="2"/><circle cx="24" cy="18" r="3" fill="#e39a3a" stroke="#fff" stroke-width="2"/></svg>
        <span>Is your classic or race car your passsion?</span></div>
    </div>
  </section>

  <section class="content">
    <article class="intro">
      <h1>Specialist engine repair &amp; reconditioning</h1>
      <h2>To have your car running at its best</h2>
      <p>Suspendisse commodo mattis velit, quis aliquam mi semper et. Pellentesque lacinia malesuada ante, eget porta nibh. In eget est eu turpis tincidunt iaculis id sit amet purus. Etiam a lorem luctus, tincidunt quam sit amet, gravida dui. Donec arcu augue, egestas vitae nisi sit amet, congue gravida nulla. Nullam laoreet ligula non augue venenatis suscipit. Suspendisse potenti. Proin malesuada, lectus at semper feugiat, justo nisi pharetra eros, convallis facilisis dui orci ac nisl commodo mattis velit, quis aliquam mi semper.</p>
      <ul class="checklist">
        <li>Do you have a personal or family car that needs a repair?</li>
        <li>Have a classic car that needs specialist engine work?</li>
        <li>Own a race car that needs specialist engine repairs?</li>
        <li>Are you a garage owner, needing to outsource an engine machining job from one of your customers?</li>
      </ul>
      <div class="partners">
        <div class="badge-square" role="img" aria-label="Partner badge"></div>
        <div class="badge-oval" role="img" aria-label="Industry association badge"></div>
      </div>
    </article>

    <aside class="quote">
      <h3>Get a Free Quote</h3>
      <form>
        <div class="field">Name</div>
        <div class="field">E-mail</div>
        <div class="field">Phone</div>
        <div class="field select"><span>Region</span><span>⇕</span></div>
        <div class="trade">Trade Customer : <span class="box"></span><b>Yes</b></div>
        <div class="field area">Details</div>
        <span class="submit">SUBMIT</span>
      </form>
    </aside>
  </section>
</main>

<footer class="site-footer">
  <div class="wrap">
    <ul class="foot-nav">
      <li>Home</li><li>About us</li><li>Private Vehicle Service &amp; Repair</li><li>Trade Customers</li><li>Race &amp; Classic Car Engine</li><li>Make an Enquiry</li><li>Contact us</li>
    </ul>
    <div class="foot-bottom">
      <div class="copy">Copyright © 2014 Harlow Bay Engine Reconditioners. All rights reserved.</div>
      <div class="social">
        <span style="background:#3b5a9a"></span><span style="background:#29a9e1"></span><span style="background:#1e87c0"></span><span style="background:#f27022"></span>
      </div>
    </div>
  </div>
</footer>
</body>
</html>
```